Front and content page design for Fitness Cookbook

I am looking for someone to Design a front cover for a Recipe book and also create an amazing layout for the book.

Its for a corporate seminar so has to be eye catching, professional and bold.

Content is complete

Target Market(s)

Industry/Entity Type

Health And Wellness

Font styles to use
Sans Serif

Requirements
Must have
• Eye catching, professional and bold.
• By Dorian as stated on the document
• Must have Tidewell Motion Logo on it.

```html
<!DOCTYPE html>
<html lang="en">
<head>
<meta charset="utf-8">
<title>Protein and Fat Meals</title>
<link href="https://fonts.googleapis.com/css2?family=Oswald:wght@500&family=Open+Sans:wght@400;600;700&display=swap" rel="stylesheet">
<style>
  :root {
    --page-bg: #fde6cc;
    --accent: #f18a1f;
    --ink: #3a3530;
  }
  html, body {
    margin: 0;
    padding: 0;
    overflow: hidden;
  }
  .page {
    position: relative;
    width: 849px;
    height: 1200px;
    background: var(--page-bg);
    font-family: "Open Sans", Arial, sans-serif;
    color: var(--ink);
    overflow: hidden;
  }
  .content {
    position: absolute;
    left: 95px;
    top: 278px;
    width: 660px;
  }
  .page-title {
    font-family: "Oswald", "Arial Narrow", sans-serif;
    font-weight: 500;
    font-size: 52px;
    line-height: 1;
    color: var(--accent);
    margin: 0 0 22px;
    letter-spacing: -0.5px;
  }
  .section-heading {
    font-size: 25px;
    font-weight: 600;
    margin: 0 0 8px;
    letter-spacing: -0.2px;
  }
  .point-list {
    list-style: none;
    margin: 0 0 20px;
    padding: 0;
    font-size: 13px;
    font-weight: 600;
    line-height: 1.62;
  }
  .point-list li::before {
    content: "- ";
  }
</style>
</head>
<body>
<main class="page">
  <section class="content">
    <h1 class="page-title">Protein and Fat Meals</h1>

    <h2 class="section-heading">Best used:</h2>
    <ul class="point-list">
      <li>Anytime of the day other than around training (goal dependent)</li>
      <li>Rest days</li>
      <li>Breakfasts (especially meals containing red meat)</li>
      <li>During a low carb or ‘reset’ plan/phase</li>
    </ul>

    <h2 class="section-heading">Why eat these meals:</h2>
    <ul class="point-list">
      <li>To help regulate blood sugar levels throughout the day</li>
      <li>To ‘teach’ your body to use fats as fuel, resulting in greater fat loss long term</li>
      <li>To keep you fuller for longer</li>
      <li>To help ‘clean out’ your digestive system and liver pathways</li>
      <li>Increase mental focus and awareness</li>
    </ul>
  </section>
</main>
</body>
</html>
```